Mira Bloom Fitness Coaching Project

I am a personal trainer based in London. My services include one-on-one PT sessions, bootcamps.
I would like the design to be minimalistic. With light colours: white, pink, purple.
I specialise in weight loss, flexibility, mobility.

Tessa Brogan
Personal Trainer
Email: tessa.brogan@quellmail.com
tel: 07700218493
Instagram: Mira Bloom

Target Market(s)

adults, mostly females (age 18-50).

Industry/Entity Type

Fitness

Contact Information for Business Card

Tessa Brogan
Personal Trainer
tel: 07700218493
Instagram: Mira Bloom

Font styles to use
Serif

Colors
eea4c8
fbd4d5
fdf9cf
cfeae6
cee9f5

Requirements
Nice to have
• minimalistic style
• easy to read and remember

```html
<!DOCTYPE html>
<html lang="en">
<head>
<meta charset="utf-8">
<title>Tessa Brogan – Business Card</title>
<link rel="stylesheet" href="https://fonts.googleapis.com/css2?family=Anton&family=Roboto:wght@400;500&display=swap">
<style>
  :root {
    --stage: #e8e5e2;
    --card-frost: #f3f1f2;
    --card-frost-edge: #e6e2e6;
    --purple: #5a2a63;
    --purple-band: #4f2557;
    --band-text: #f1e3ee;
    --text-grey: #4a4548;
    --photo-pink: #dc3f7c;
    --photo-pink-deep: #c22c67;
    --photo-teal: #2e9e97;
    --photo-teal-deep: #1f7f7c;
    --photo-ground: #3b3537;
    --portrait-warm: #8a5a44;
    --portrait-dark: #3f2a22;
  }
  * { box-sizing: border-box; margin: 0; padding: 0; }
  html, body {
    width: 1200px;
    height: 969px;
    overflow: hidden;
    background: var(--stage);
  }
  .business-card {
    position: absolute;
    left: 100px;
    top: 201px;
    width: 1000px;
    height: 567px;
    border-radius: 26px;
    overflow: hidden;
    background: linear-gradient(135deg, var(--card-frost) 0%, var(--card-frost-edge) 100%);
    box-shadow: 0 10px 30px rgba(0, 0, 0, 0.12);
  }
  .action-photo {
    position: absolute;
    top: 0;
    right: 0;
    width: 720px;
    height: 100%;
    background:
      linear-gradient(180deg,
        var(--photo-pink-deep) 0%,
        var(--photo-pink) 45%,
        var(--photo-teal) 55%,
        var(--photo-teal-deep) 82%,
        var(--photo-ground) 100%);
    -webkit-mask-image: linear-gradient(90deg, transparent 0%, rgba(0,0,0,0.35) 22%, #000 42%);
    mask-image: linear-gradient(90deg, transparent 0%, rgba(0,0,0,0.35) 22%, #000 42%);
  }
  .portrait {
    position: absolute;
    left: 56px;
    top: 55px;
    width: 154px;
    height: 166px;
    border-radius: 10px;
    background: radial-gradient(circle at 50% 45%, var(--portrait-warm) 0%, var(--portrait-dark) 80%);
  }
  .trainer-name {
    position: absolute;
    left: 56px;
    top: 236px;
    font-family: "Anton", sans-serif;
    font-size: 60px;
    line-height: 1;
    color: var(--purple);
    letter-spacing: 0.5px;
  }
  .trainer-role {
    position: absolute;
    left: 58px;
    top: 308px;
    font-family: "Roboto", sans-serif;
    font-weight: 500;
    font-size: 25px;
    color: var(--text-grey);
  }
  .contact-list {
    position: absolute;
    left: 58px;
    top: 354px;
    list-style: none;
    font-family: "Roboto", sans-serif;
    font-size: 24px;
    color: var(--text-grey);
  }
  .contact-list li {
    display: flex;
    align-items: center;
    height: 32px;
  }
  .contact-icon {
    width: 20px;
    height: 20px;
    margin-right: 14px;
    flex: none;
  }
  .social-mark {
    width: 16px;
    height: 16px;
    margin: 0 16px 0 2px;
    background: var(--purple);
    border-radius: 3px;
    flex: none;
  }
  .services-band {
    position: absolute;
    left: 43px;
    top: 468px;
    width: 314px;
    height: 48px;
    background: var(--purple-band);
    display: flex;
    align-items: center;
    padding-left: 22px;
    font-family: "Roboto", sans-serif;
    font-size: 23px;
    color: var(--band-text);
  }
</style>
</head>
<body>
  <div class="business-card">
    <div class="action-photo" role="img" aria-label="Photo of a trainer mid high kick in front of a pink and teal painted brick wall"></div>

    <div class="portrait" role="img" aria-label="Portrait photo of Tessa Brogan"></div>

    <h1 class="trainer-name">Tessa Brogan</h1>
    <p class="trainer-role">Personal Trainer</p>

    <ul class="contact-list">
      <li>
        <svg class="contact-icon" viewBox="0 0 24 24" aria-hidden="true">
          <path fill="#5a2a63" d="M6.6 10.8a15.2 15.2 0 0 0 6.6 6.6l2.2-2.2a1 1 0 0 1 1-.25 11.4 11.4 0 0 0 3.6.57 1 1 0 0 1 1 1V20a1 1 0 0 1-1 1A17 17 0 0 1 3 4a1 1 0 0 1 1-1h3.5a1 1 0 0 1 1 1c0 1.25.2 2.45.57 3.57a1 1 0 0 1-.25 1z"/>
        </svg>
        07700218493
      </li>
      <li>
        <svg class="contact-icon" viewBox="0 0 24 24" aria-hidden="true">
          <path fill="#5a2a63" d="M3 5h18a1 1 0 0 1 1 1v12a1 1 0 0 1-1 1H3a1 1 0 0 1-1-1V6a1 1 0 0 1 1-1zm9 7.2L20 7H4z"/>
        </svg>
        tessa.brogan@quellmail.com
      </li>
      <li>
        <span class="social-mark" aria-hidden="true"></span>
        Mira Bloom
      </li>
    </ul>

    <div class="services-band">PT sessions, bootcamps.</div>
  </div>
</body>
</html>
```